Company Website Re-design for Software development consultancy

We would like our company website to be redesigned using our existing marketing collateral and website content as a guide

current site : www.brightkestrel.com.au

For the different pages types and content please base on the following site : https://www.quorvalabs.net/

We want a coded site - but will replace the content ourselves within the sections you provide to customise to our needs.

Target Market(s)

Medium to Large corporates needing software design and development services

Industry/Entity Type

Information Technology

Coding

Coded - Design and coding required

Number of Pages Required

5+ page

Font styles to use
Sans Serif

Colors
ec1f27
ffffff
000000

Requirements
Must have
• Align to colour scheme of existing collateral
• Include pages for the key areas of our busines - see : https://www.quorvalabs.net/
Nice to have
• image rotators - make the site interesting to the business visitor

```html
<!DOCTYPE html>
<html lang="en">
<head>
<meta charset="utf-8">
<title>Bright Kestrel – Contact</title>
<link rel="stylesheet" href="https://fonts.googleapis.com/css2?family=Poppins:wght@600;700&family=Roboto:wght@400;500&family=Open+Sans:wght@400&display=swap">
<style>
  :root {
    --red: #ec1f27;
    --red-form: #e60023;
    --red-dark: #8a0a10;
    --black: #000000;
    --white: #ffffff;
    --ink: #1a1a1a;
    --grey-text: #666666;
    --band-dark: #2c2c2c;
  }
  * { box-sizing: border-box; margin: 0; padding: 0; }
  html, body { width: 937px; height: 1200px; overflow: hidden; background: var(--white); }
  .page { position: relative; width: 937px; height: 1200px; overflow: hidden; font-family: "Roboto", Arial, sans-serif; color: var(--ink); }

  /* Hero */
  .hero { position: absolute; left: 0; top: 0; width: 937px; height: 342px;
    background: radial-gradient(ellipse at 60% 40%, #6b5a4a 0%, #3f3731 45%, #231f1c 100%); }
  .brand { position: absolute; left: 142px; top: 24px; font-family: "Poppins", sans-serif; font-weight: 700;
    font-size: 27px; letter-spacing: 0.5px; color: var(--white); line-height: 1; }
  .nav { position: absolute; top: 32px; left: 376px; display: flex; gap: 26px; list-style: none; }
  .nav a { color: var(--white); text-decoration: none; font-size: 12px; font-weight: 500; letter-spacing: 0.2px; }
  .hero-mark { position: absolute; left: 431px; top: 121px; width: 62px; height: 62px; border: 4px solid var(--red); border-radius: 50%; }
  .hero-title { position: absolute; left: 0; width: 937px; top: 188px; text-align: center;
    font-family: "Poppins", sans-serif; font-weight: 600; font-size: 37px; color: var(--white); }

  /* Contact info */
  .contact-heading { position: absolute; left: 141px; top: 403px; font-family: "Poppins", sans-serif; font-weight: 600; font-size: 23px; color: var(--black); }
  .contact-intro { position: absolute; left: 140px; top: 441px; width: 620px; font-family: "Open Sans", sans-serif; font-size: 11.5px; line-height: 20px; color: var(--grey-text); }
  .info { position: absolute; top: 511px; }
  .info-icon { width: 54px; height: 54px; border-radius: 50%; background: var(--black); display: flex; align-items: center; justify-content: center; }
  .info-label { margin: 13px 0 0 6px; font-size: 13px; font-weight: 500; color: var(--ink); }
  .info-value { margin: 3px 0 0 6px; font-size: 15px; color: var(--ink); white-space: nowrap; }

  /* Form band */
  .band { position: absolute; left: 0; top: 690px; width: 937px; height: 460px; }
  .form-heading { position: absolute; left: 0; width: 944px; top: 761px; text-align: center; font-family: "Poppins", sans-serif; font-weight: 600; font-size: 22px; color: var(--white); }
  .contact-form { position: absolute; left: 162px; top: 811px; width: 616px; height: 234px; background: var(--red-form); }
  .field { position: absolute; border: none; border-bottom: 1.5px solid var(--white); background: transparent;
    color: var(--white); font-family: "Roboto", sans-serif; font-size: 12px; padding: 0 2px 5px; outline: none; }
  .field::placeholder { color: var(--white); opacity: 1; }
  .field-name { left: 27px; top: 44px; width: 273px; height: 22px; }
  .field-email { left: 27px; top: 83px; width: 273px; height: 22px; }
  .field-phone { left: 27px; top: 122px; width: 273px; height: 22px; }
  .field-message { left: 323px; top: 50px; width: 273px; height: 94px; resize: none; padding-top: 0; }
  .submit { position: absolute; left: 29px; top: 159px; width: 122px; height: 35px; background: var(--ink); color: var(--white);
    border: none; font-family: "Roboto", sans-serif; font-size: 13px; font-weight: 500; }

  /* Footer */
  .footer-note { position: absolute; left: 297px; top: 1157px; font-family: "Open Sans", sans-serif; font-size: 12px; color: #444; white-space: nowrap; }
  .social { position: absolute; top: 1164px; left: 670px; display: flex; gap: 20px; list-style: none; }
  .social li { width: 16px; height: 16px; border-radius: 50%; background: #555; }
</style>
</head>
<body>
<div class="page">

  <header class="hero" role="img" aria-label="Photo of a desk with laptop, notebook, coffee cup and plant, darkened">
    <div class="brand">BRIGHT KESTREL</div>
    <ul class="nav">
      <li><a href="#">ABOUT US</a></li>
      <li><a href="#">PRODUCTS AND SERVICES</a></li>
      <li><a href="#">BLOG ARTICLE</a></li>
      <li><a href="#">CONTACT</a></li>
    </ul>
    <div class="hero-mark"></div>
    <h1 class="hero-title">CONTACT</h1>
  </header>

  <h2 class="contact-heading">CONTACT US</h2>
  <p class="contact-intro">Aonsectetuer mi a ultricies massa est sed nisl Class aptent taciti sociosqu ad litora torquent per conubia nostra per inceptos hymenaeos Proin nulla arcu nonummy luctus dictum eget fermentum et lorem</p>

  <div class="info" style="left:139px">
    <div class="info-icon">
      <svg width="18" height="24" viewBox="0 0 18 24"><path d="M9 0C4 0 0 4 0 9c0 6.5 9 15 9 15s9-8.5 9-15C18 4 14 0 9 0z" fill="#ec1f27"/><circle cx="9" cy="9" r="3.3" fill="#000"/></svg>
    </div>
    <div class="info-label">ADDRESS</div>
    <div class="info-value">42 – 46 HARBOUR LN, SYDNEY 2000</div>
  </div>

  <div class="info" style="left:413px">
    <div class="info-icon">
      <svg width="22" height="22" viewBox="0 0 24 24"><path d="M6.6 10.8c1.4 2.8 3.8 5.1 6.6 6.6l2.2-2.2c.3-.3.7-.4 1-.2 1.1.4 2.3.6 3.6.6.6 0 1 .4 1 1V20c0 .6-.4 1-1 1C10.6 21 3 13.4 3 4c0-.6.4-1 1-1h3.5c.6 0 1 .4 1 1 0 1.3.2 2.5.6 3.6.1.3 0 .7-.2 1z" fill="#ec1f27"/></svg>
    </div>
    <div class="info-label">PHONE NUMBER</div>
    <div class="info-value">(666) 555 0182</div>
  </div>

  <div class="info" style="left:606px">
    <div class="info-icon">
      <svg width="26" height="20" viewBox="0 0 26 20"><rect x="0" y="0" width="26" height="20" rx="2" fill="#ec1f27"/><path d="M1 2l12 9 12-9" stroke="#000" stroke-width="2.2" fill="none"/></svg>
    </div>
    <div class="info-label">EMAIL US</div>
    <div class="info-value">INFO@BRIGHTKESTREL.COM.AU</div>
  </div>

  <svg class="band" width="937" height="460" viewBox="0 690 937 460" role="img" aria-label="Dark photo of a workspace with network line pattern behind the contact form">
    <defs>
      <linearGradient id="bandShade" x1="0" y1="0" x2="1" y2="1">
        <stop offset="0" stop-color="#3a3a3a"/>
        <stop offset="1" stop-color="#262626"/>
      </linearGradient>
    </defs>
    <polygon points="0,694 720,726 937,726 937,1144 0,1104" fill="url(#bandShade)"/>
    <polygon points="720,726 937,704 937,734" fill="var(--red)"/>
    <polygon points="720,726 937,704 937,716" fill="var(--red-dark)"/>
    <polygon points="0,1104 212,1112 0,1134" fill="var(--red)"/>
    <polygon points="0,1104 212,1112 0,1120" fill="var(--red-dark)"/>
  </svg>

  <h2 class="form-heading">CONTACT FORM</h2>
  <form class="contact-form">
    <input class="field field-name" type="text" placeholder="NAME" aria-label="Name">
    <input class="field field-email" type="email" placeholder="EMAIL" aria-label="Email">
    <input class="field field-phone" type="tel" placeholder="PHONE NUMBER" aria-label="Phone number">
    <textarea class="field field-message" placeholder="MESSAGE" aria-label="Message"></textarea>
    <button class="submit" type="button">SUBMIT</button>
  </form>

  <footer>
    <p class="footer-note">© 2018 Company Name &nbsp;All right reserved &nbsp;Term of Use</p>
    <ul class="social" aria-label="Social links">
      <li></li><li></li><li></li><li></li>
    </ul>
  </footer>

</div>
</body>
</html>
```